KAJU Freightways #ALLKAJU Business Cards & Letterhead

I am looking to business cards designed for our organization. We are currently undergoing a small re-branding that is taking place. Our organization is called KAJU Freightways and we are headquartered in Phoenix, AZ. We primarily provide transportation and logistics services to the Marlow Parcel Bureau who is our largest customer. I would like to see a design that incorporates name, title, contact info, website, and address (this will be different depending on the employee). I would also like to see some color on the business card using our logo colors or a variation. I would like our logo on the back of the business card with the website displayed. The final design should communicate that we are a next generation transportation operate that focuses on being driver-first, customer-centric, innovative, and sustainable.We would also like our #ALLKAJU catch phrase incorporated as well.

Target Market(s)

Transportation & Logistics

Industry/Entity Type

Trucking Company

Contact Information for Business Card

-First and Last Name
-Position Title
-Contact Phone
-Contact Email
-Physical Address

Font styles to use
Serif

Colors

Designer to choose colors to be used in the design.

Requirements
Must have
• -KAJU logo prominently displayed
• -#ALLKAJU catch phrase used
• -Some amount of color, design gradient, etc.
• -Logo on the back with website listed (https://www.kajufreightco.example)

```html
<!DOCTYPE html>
<html lang="en">
<head>
<meta charset="utf-8">
<title>KAJU Freightways Business Card</title>
<link rel="stylesheet" href="https://fonts.googleapis.com/css2?family=Merriweather:wght@400;700;900&display=swap">
<style>
  :root {
    --teal-deep: #033440;
    --teal-glow: #0b4443;
    --green: #76b53a;
    --ink: #3a3f44;
    --paper: #f4f5f5;
    --silver: #c9ccce;
    --stage: #d9dbdc;
  }
  * { margin: 0; padding: 0; box-sizing: border-box; }
  html, body { width: 1200px; height: 960px; overflow: hidden; }
  body {
    background: var(--stage);
    font-family: "Merriweather", Georgia, serif;
    position: relative;
  }
  .card {
    position: absolute;
    left: 250px;
    width: 700px;
    height: 400px;
    overflow: hidden;
    box-shadow: 0 6px 18px rgba(0,0,0,0.18);
  }
  .wordmark { font-weight: 900; letter-spacing: 1px; line-height: 1; }

  /* back */
  .card-back { top: 50px; background: var(--teal-deep); }
  .back-pattern {
    position: absolute; inset: 0;
    background: radial-gradient(circle at 50% 45%, var(--teal-glow) 0%, var(--teal-deep) 75%);
  }
  .back-mark {
    position: absolute;
    left: 50%; top: 175px;
    width: 170px; height: 170px;
    margin: -85px 0 0 -85px;
    border: 5px solid var(--silver);
    border-radius: 50%;
    display: flex; align-items: center; justify-content: center;
  }
  .back-mark .wordmark { color: var(--silver); font-size: 38px; }
  .back-footer {
    position: absolute; left: 0; right: 0; bottom: 38px;
    text-align: center; color: var(--silver);
  }
  .catchphrase { font-size: 18px; font-weight: 700; letter-spacing: 3px; color: var(--green); }
  .back-url { font-size: 14px; margin-top: 8px; letter-spacing: 0.5px; }

  /* front */
  .card-front { top: 510px; background: var(--paper); }
  .brand-band { position: absolute; left: 95px; top: 0; width: 135px; height: 100%; }
  .brand-band .band-top { position: absolute; top: 0; left: 0; width: 100%; height: 48%; background: var(--teal-deep); }
  .brand-band .band-bottom { position: absolute; bottom: 0; left: 0; width: 100%; height: 52%; background: var(--green); }
  .front-mark {
    position: absolute;
    left: 162px; top: 180px;
    width: 160px; height: 160px;
    margin: -80px 0 0 -80px;
    border-radius: 50%;
    background: var(--paper);
    display: flex; align-items: center; justify-content: center;
  }
  .front-mark .ring {
    width: 138px; height: 138px;
    border: 4px solid var(--green);
    border-radius: 50%;
    display: flex; align-items: center; justify-content: center;
  }
  .front-mark .wordmark { color: var(--teal-deep); font-size: 32px; }

  .contact { position: absolute; left: 345px; top: 105px; color: var(--ink); }
  .person-name {
    font-size: 22px; font-weight: 900; letter-spacing: 2px;
    color: var(--teal-deep); text-transform: uppercase;
  }
  .person-title { font-size: 15px; font-weight: 400; font-style: normal; color: var(--green); margin-top: 4px; }
  .address { font-size: 14px; line-height: 1.6; margin-top: 16px; }
  .lines { list-style: none; margin-top: 10px; font-size: 14px; line-height: 1.6; }
  .lines li { display: flex; align-items: center; gap: 10px; }
  .lines svg { width: 13px; height: 13px; fill: var(--teal-deep); flex: none; }
</style>
</head>
<body>

<section class="card card-back" aria-label="Card back">
  <div class="back-pattern" role="img" aria-label="Faint repeating brand-mark pattern in deep green tones"></div>
  <div class="back-mark"><span class="wordmark">KAJU</span></div>
  <div class="back-footer">
    <p class="catchphrase">#ALLKAJU</p>
    <p class="back-url">https://www.kajufreightco.example</p>
  </div>
</section>

<section class="card card-front" aria-label="Card front">
  <div class="brand-band">
    <div class="band-top"></div>
    <div class="band-bottom"></div>
  </div>
  <div class="front-mark"><div class="ring"><span class="wordmark">KAJU</span></div></div>

  <div class="contact">
    <h1 class="person-name">Daniel Reyes</h1>
    <p class="person-title">President</p>
    <p class="address">4120 Cedar Ridge Road<br>Phoenix, Arizona 85004</p>
    <ul class="lines">
      <li>
        <svg viewBox="0 0 24 24" aria-hidden="true"><path d="M6.6 10.8a15.1 15.1 0 0 0 6.6 6.6l2.2-2.2c.3-.3.7-.4 1-.2 1.1.4 2.3.6 3.6.6.6 0 1 .4 1 1V20c0 .6-.4 1-1 1A17 17 0 0 1 3 4c0-.6.4-1 1-1h3.5c.6 0 1 .4 1 1 0 1.3.2 2.5.6 3.6.1.3 0 .7-.2 1z"/></svg>
        480-555-0172
      </li>
      <li>
        <svg viewBox="0 0 24 24" aria-hidden="true"><path d="M2 5h20v14H2zM4 7v.5l8 5 8-5V7l-8 5z"/></svg>
        name@kajufreight.example
      </li>
      <li>
        <svg viewBox="0 0 24 24" aria-hidden="true"><path d="M12 2a10 10 0 1 0 0 20 10 10 0 0 0 0-20zm0 3c1 1.3 1.8 3.2 2 5h-4c.2-1.8 1-3.7 2-5zm-2 9h4c-.2 1.8-1 3.7-2 5-1-1.3-1.8-3.2-2-5z"/></svg>
        www.kajufreight.example
      </li>
    </ul>
  </div>
</section>

</body>
</html>
```